Melorix artwork for new single release

I need Melorix artwork creating to release a new single on there.

The specs are:

Ideal size: 3000 x 3000 pixels
Minimum size: 1400 x 1400 pixels
Aspect ratio: 1:1 (must be a perfect square)
File format: JPG or PNG
Color space: sRGB
File size: Max 4MB

The song is called "Was It Ever Rain?"
The artist is "Martin Hollow"

We have no images of Martin, so it really is open to imagination.

Target Market(s)

Melorix listeners

Industry/Entity Type

Music

```html
<!DOCTYPE html>
<html lang="en">
<head>
<meta charset="utf-8">
<title>Was It Ever Rain? – Martin Hollow</title>
<link rel="stylesheet" href="https://fonts.googleapis.com/css2?family=Gloria+Hallelujah&family=Great+Vibes&display=swap">
<style>
  :root {
    --sky-top: #3d12b8;
    --sky-upper: #6a22e6;
    --sky-mid: #b43ae8;
    --sky-glow: #ef5cd0;
    --sky-horizon: #f79a78;
    --sea-top: #6a36c8;
    --sea-mid: #3a2db0;
    --sea-deep: #1c1566;
    --ink: #ffffff;
  }
  * { margin: 0; padding: 0; box-sizing: border-box; }
  html, body {
    width: 1200px;
    height: 1200px;
    overflow: hidden;
    background: var(--sky-top);
  }
  .cover {
    position: relative;
    width: 1200px;
    height: 1200px;
    overflow: hidden;
  }
  .scene {
    position: absolute;
    inset: 0;
    background: linear-gradient(
      180deg,
      var(--sky-top) 0%,
      var(--sky-upper) 25%,
      var(--sky-mid) 42%,
      var(--sky-glow) 55%,
      var(--sky-horizon) 63%,
      var(--sea-top) 68%,
      var(--sea-mid) 82%,
      var(--sea-deep) 100%
    );
  }
  .title-word {
    position: absolute;
    color: var(--ink);
    font-family: "Gloria Hallelujah", cursive;
    line-height: 1;
    white-space: nowrap;
  }
  .title-word--first  { left: 132px; top: 62px;  font-size: 112px; }
  .title-word--second { left: 350px; top: 190px; font-size: 100px; }
  .title-word--accent {
    left: 605px; top: 305px;
    font-family: "Great Vibes", cursive;
    font-size: 130px;
  }
  .title-word--last   { left: 876px; top: 418px; font-size: 112px; }
  .artist {
    position: absolute;
    left: 828px;
    top: 652px;
    color: var(--ink);
    font-family: "Gloria Hallelujah", cursive;
    font-size: 44px;
    line-height: 1;
    white-space: nowrap;
  }
</style>
</head>
<body>
  <main class="cover">
    <div class="scene" role="img" aria-label="Illustration of a tropical beach at sunset with palm trees, a purple and pink sky, calm ocean waves and a silhouetted couple embracing on the sand"></div>
    <h1 class="title">
      <span class="title-word title-word--first">Was</span>
      <span class="title-word title-word--second">It</span>
      <span class="title-word title-word--accent">Ever</span>
      <span class="title-word title-word--last">Rain?</span>
    </h1>
    <p class="artist">Martin Hollow</p>
  </main>
</body>
</html>
```